Dusty Spur Outfitters Home Page

I need a logo and page design for my home page, maybe some background color suggestions to go with it. I want the logo to project "vintage" and "western wear" but not be your typical trite western saddle and gun type thing.
http://www.dustyspuroutfitters.example/store/cart.php
Not looking for page coding just logo and other design elements to lay in over the site's template to make it "pop"
Reason: Have to finalize the design.
Target Market(s)
My customers are 70/30 men to women.
Industry/Entity Type
Gun

```html
<!DOCTYPE html>
<html lang="en">
<head>
<meta charset="utf-8">
<title>Dusty Spur Outfitters — Header Options</title>
<link rel="stylesheet" href="https://fonts.googleapis.com/css2?family=Dancing+Script:wght@700&family=Lato:wght@700;900&display=swap">
<style>
  :root {
    --linen: #d3c1a1;
    --linen-light: #dac9aa;
    --linen-dark: #c9b695;
    --teal: #4a949c;
    --teal-dark: #3f858d;
    --band-charcoal: #2b2b2b;
    --band-charcoal-light: #3a3a3a;
    --band-leather: #1d1d1f;
    --band-leather-light: #2a2a2c;
    --band-slate: #2e2e2e;
    --band-slate-light: #434343;
    --cream: #ecdcb6;
    --tagline: #d6cab0;
    --field: #e6d9bd;
    --field-text: #333028;
    --go: #e2d6ba;
    --brand-red: #b5301c;
  }

  * { margin: 0; padding: 0; box-sizing: border-box; }

  html, body {
    width: 1200px;
    height: 1000px;
    overflow: hidden;
  }

  body {
    position: relative;
    background:
      repeating-linear-gradient(90deg, rgba(255,255,255,0.05) 0 1px, transparent 1px 3px),
      repeating-linear-gradient(0deg, rgba(0,0,0,0.04) 0 1px, transparent 1px 3px),
      linear-gradient(180deg, var(--linen-light), var(--linen) 50%, var(--linen-dark));
    font-family: "Lato", Arial, sans-serif;
  }

  .header-option {
    position: absolute;
    left: 0;
    width: 1200px;
    height: 165px;
    box-shadow: 0 3px 4px rgba(60, 40, 20, 0.35);
  }
  .header-option--one { top: 147px; }
  .header-option--two { top: 417px; }
  .header-option--three { top: 687px; }

  .trim {
    position: absolute;
    left: 0;
    width: 100%;
    height: 16px;
    background: linear-gradient(180deg, var(--teal), var(--teal-dark));
  }
  .trim--top { top: 0; }
  .trim--bottom { bottom: 0; }

  .band {
    position: absolute;
    top: 16px;
    left: 0;
    width: 100%;
    height: 133px;
  }
  .band--charcoal {
    background:
      radial-gradient(ellipse at 70% 30%, var(--band-charcoal-light), transparent 60%),
      radial-gradient(ellipse at 15% 80%, var(--band-charcoal-light), transparent 55%),
      var(--band-charcoal);
  }
  .band--leather {
    background:
      radial-gradient(ellipse at 80% 60%, var(--band-leather-light), transparent 60%),
      linear-gradient(180deg, var(--band-leather-light), var(--band-leather));
  }
  .band--slate {
    background:
      radial-gradient(ellipse at 30% 70%, var(--band-slate-light), transparent 60%),
      radial-gradient(ellipse at 90% 20%, var(--band-slate-light), transparent 50%),
      var(--band-slate);
  }

  .brand {
    position: absolute;
    left: 62px;
    top: 64px;
    display: flex;
    align-items: center;
    gap: 10px;
    white-space: nowrap;
  }
  .brand-mark {
    width: 16px;
    height: 16px;
    border-radius: 50%;
    background: var(--brand-red);
  }
  .brand-name {
    font-weight: 900;
    font-size: 26px;
    letter-spacing: 0.5px;
    line-height: 32px;
    color: var(--cream);
    text-transform: uppercase;
  }

  .tagline {
    position: absolute;
    left: 476px;
    top: 86px;
    font-family: "Dancing Script", cursive;
    font-weight: 700;
    font-size: 25px;
    line-height: 30px;
    color: var(--tagline);
    white-space: nowrap;
  }

  .search {
    position: absolute;
    left: 901px;
    top: 51px;
    display: flex;
    align-items: center;
    gap: 11px;
  }
  .search-field {
    width: 172px;
    height: 30px;
    border-radius: 15px;
    background: var(--field);
    padding-left: 17px;
    font-weight: 700;
    font-size: 17px;
    line-height: 30px;
    color: var(--field-text);
  }
  .search-go {
    font-weight: 700;
    font-size: 18px;
    color: var(--go);
  }
</style>
</head>
<body>

  <header class="header-option header-option--one">
    <div class="trim trim--top"></div>
    <div class="band band--charcoal" role="img" aria-label="Distressed charcoal grunge texture"></div>
    <div class="trim trim--bottom"></div>
    <div class="brand"><span class="brand-mark"></span><span class="brand-name">Dusty Spur Outfitters</span></div>
    <p class="tagline">Brand-New Retro Styled Western Wear</p>
    <div class="search"><span class="search-field">Search...</span><span class="search-go">GO!</span></div>
  </header>

  <header class="header-option header-option--two">
    <div class="trim trim--top"></div>
    <div class="band band--leather" role="img" aria-label="Black pebbled leather texture"></div>
    <div class="trim trim--bottom"></div>
    <div class="brand"><span class="brand-mark"></span><span class="brand-name">Dusty Spur Outfitters</span></div>
    <p class="tagline">Brand-New Retro Styled Western Wear</p>
    <div class="search"><span class="search-field">Search...</span><span class="search-go">GO!</span></div>
  </header>

  <header class="header-option header-option--three">
    <div class="trim trim--top"></div>
    <div class="band band--slate" role="img" aria-label="Weathered slate grey grunge texture"></div>
    <div class="trim trim--bottom"></div>
    <div class="brand"><span class="brand-mark"></span><span class="brand-name">Dusty Spur Outfitters</span></div>
    <p class="tagline">Brand-New Retro Styled Western Wear</p>
    <div class="search"><span class="search-field">Search...</span><span class="search-go">GO!</span></div>
  </header>

</body>
</html>
```